Marrowind - IT Consultancy Website

Our company is called Marrowind and our purpose is to help companies sustainably embrace and reap the benefits of cloud platforms, through transforming practices, skills and technology using DevOps and Security practices such that they are able to automate, manage and secure their cloud platforms to deliver product to market with increasing velocity.

To get our business started I require a website that will model the typical layout of an IT consultancy services company to an Australian Market. There are many examples of such a site, here are some of them. We would like a landing page and then a few simple menu options (About, Blog, Services etc..) to additional content

http://pelvo.com.au/
http://www.brisket.com.au/
http://www.tandu.com.au/

I require the site to be created with a separate CSS file that maintains the colour palette. This is a very important requirement, I want to be able to change the colours employed in the site in a single location and not have to scan through multiple files to replace the codes.

The website must be built using static content as it will not be hosted on a web server but instead in QNT using S3 and CloudFront CDN. Therefore please stick to HTML, JavaScript, CSS and other static file formats. The website needs to be response, smooth and reactive. It should render on desktop, mobile and tablet and feature smooth scrolling, transitions and fade in's.

The website should give the customer confidence that they are dealing with a highly professional IT services company, focused strongly on cloud (QNT, Vantrel Skyline, Horvik Vapor etc..), motivated by beautiful and fluid design.

In order to make this simpler for you, the designer, I have already purchased this template from https://skinmarketly.com/theme/the-venture-allround-template-KX7Q41093 and uploaded it. Feel free to use this template if you choose (note that it makes use of a separate color palette which is a key requirement) or use one of your own choosing. If you do use this template ensure that it does not look too much like "another bootstrap site" therefore use the layout and widgets but make the site look fresh and original too.
Obviously you must delete all trace of the bootstrap package once the project has completed if you do use it

Target Market(s)

Corporate and medium enterprise businesses

Industry/Entity Type

Information Technology

Coding

Coded - Design and coding required

Number of Pages Required

4 page

Font styles to use
Sans Serif

Colors
abd036
33a6d7

Requirements
Must have
• The website should give the customer confidence that they are dealing with a highly professional IT services company, focused strongly on cloud (QNT, Vantrel Skyline, Horvik Vapor etc..), motivated by beautiful and fluid design. Our company name is Marrowind, the site needs to pay homage to the themes of fluidity and logic
• Along with About Us, Services and a Blog page could I also get social logo's included too
Nice to have
• The website must be built using static content as it will not be hosted on a web server but instead in QNT using S3 and CloudFront CDN. Therefore please stick to HTML, JavaScript, CSS and other static file formats. The website needs to be response, smooth and reactive. It should render on desktop, mobile and tablet and feature smooth scrolling, transitions and fade in's.
Should not have
• Lurid colours, or too much animations. The design must "flow"

```html
<!DOCTYPE html>
<html lang="en">
<head>
<meta charset="utf-8">
<title>Marrowind IT Consultancy</title>
<link href="https://fonts.googleapis.com/css2?family=Raleway:wght@300;400;500;600;700&family=Open+Sans:wght@400;600&display=swap" rel="stylesheet">
<style>
:root{
  --blue:#1fa8e0;
  --blue-deep:#1596cc;
  --navy:#2b3248;
  --ink:#222831;
  --text:#6f7378;
  --muted:#9a9ea3;
  --dark-btn:#2b2b2b;
  --light:#f3f4f5;
  --bar:#e4e5e6;
  --white:#ffffff;
  --line:#e7e8ea;
}
*{box-sizing:border-box;margin:0;padding:0}
html,body{width:1200px;height:3237px;overflow:hidden}
body{font-family:"Open Sans",Arial,sans-serif;color:var(--text);background:var(--white);position:relative}
.abs{position:absolute}
h1,h2,h3,h4,.raleway{font-family:"Raleway",Arial,sans-serif}
.accent{color:var(--blue)}
.btn{position:absolute;display:flex;align-items:center;justify-content:center;font-family:"Raleway",Arial,sans-serif;font-size:15px;color:var(--white)}

/* hero */
.hero{position:absolute;left:0;top:0;width:1200px;height:608px;background:linear-gradient(100deg,#c9ccd0 0%,#9ea5ab 35%,#6c747b 60%,#4a5157 100%)}
.hero-photo{position:absolute;inset:0}
.nav{position:absolute;top:0;left:0;width:1200px;height:100px}
.logo{position:absolute;left:97px;top:36px;font-family:"Raleway",Arial,sans-serif;font-size:27px;color:var(--white);letter-spacing:.2px}
.logo b{font-weight:700}
.menu{position:absolute;top:0;left:478px;display:flex;height:100px}
.menu a{display:flex;align-items:center;justify-content:center;height:100px;padding:0 23px;color:var(--white);font-family:"Raleway",Arial,sans-serif;font-size:14px;text-decoration:none;letter-spacing:.3px}
.menu a.active{background:var(--blue)}
.hero-copy{position:absolute;left:587px;top:232px;color:var(--white)}
.hero-copy .l1{font-family:"Raleway";font-size:36px;font-weight:500;line-height:40px}
.hero-copy .l2{font-family:"Raleway";font-size:44px;font-weight:600;line-height:54px}
.hero-copy .l3{font-family:"Raleway";font-size:34px;font-weight:300;line-height:44px}
.hero-btn{left:587px;top:422px;width:160px;height:54px;background:var(--blue);border:2px solid var(--white);font-size:17px}
.arrow{position:absolute;top:316px;width:32px;height:32px;border:1.5px solid rgba(255,255,255,.8);border-radius:50%}

/* welcome */
.section-title{position:absolute;left:0;width:1200px;text-align:center;font-family:"Raleway";font-weight:600;font-size:26px;color:var(--ink);letter-spacing:.3px}
.welcome-text{position:absolute;left:228px;top:716px;width:744px;text-align:center;font-size:11.6px;line-height:22px}
.btn-blue{background:var(--blue)}
.btn-dark{background:var(--dark-btn)}

/* why us */
.why{position:absolute;left:0;top:965px;width:1200px;height:237px;background:var(--navy)}
.why-box{position:absolute;left:97px;top:0;width:306px;height:237px;background:var(--blue);text-align:center;color:var(--white)}
.why-box h3{margin-top:40px;font-size:24px;font-weight:600}
.why-box p{margin:14px auto 0;width:220px;font-size:13px;line-height:20px}
.why-box .btn{left:101px;top:148px;width:104px;height:40px;font-size:13px;background:#2b2b2b}
.platform{position:absolute;top:0;width:220px;text-align:center;color:var(--white)}
.platform .mark{width:40px;height:40px;margin:50px auto 0;border:2px solid var(--white);border-radius:4px}
.platform h4{margin-top:28px;font-size:16px;font-weight:600}
.platform p{margin:6px auto 0;width:170px;font-size:12.5px;line-height:21px;color:#dfe3ea}

/* who */
.who-text{position:absolute;left:97px;top:1312px;width:485px;font-size:11.6px;line-height:22px}
.who-text p{margin-bottom:12px}
.ticks{list-style:none;margin-top:18px}
.ticks li{display:flex;align-items:center;gap:16px;height:26px}
.screen{position:absolute;left:642px;top:1316px;width:438px;height:270px;background:linear-gradient(110deg,#c6cbd0,#7f878e 60%,#4f575d);border:14px solid #1d1f22;border-radius:10px 10px 0 0}
.laptop-base{position:absolute;left:600px;top:1586px;width:522px;height:18px;background:linear-gradient(#dfe1e3,#aeb2b6);border-radius:0 0 14px 14px}

/* offers */
.offers{position:absolute;left:0;top:1668px;width:1200px;height:175px;background:linear-gradient(90deg,#15171a,#2a2621 50%,#181a1c)}
.offers h2{position:absolute;left:97px;top:38px;font-size:27px;font-weight:700;color:var(--white)}
.offers p{position:absolute;left:97px;top:84px;width:700px;font-size:12px;line-height:22px;color:var(--white)}
.offers .btn{left:828px;top:62px;width:212px;height:52px}

/* services */
.service{position:absolute;width:337px;text-align:center}
.service svg{display:block;margin:0 auto}
.service h4{margin-top:16px;font-size:17px;font-weight:500;color:var(--ink);letter-spacing:.3px}
.service p{margin:8px auto 0;width:270px;font-size:11px;line-height:21px}
.service .more{display:block;margin-top:12px;font-size:12px;color:var(--blue)}
.vline{position:absolute;width:1px;background:var(--line)}

/* testimonial */
.testi{position:absolute;left:0;top:2467px;width:1200px;height:415px;background:linear-gradient(180deg,#2aabe3,#1f9fd8)}
.testi h2{position:absolute;left:0;width:1200px;top:50px;text-align:center;font-size:26px;font-weight:600;color:var(--ink)}
.testi h2 span{color:var(--white)}
.testi .quote{position:absolute;left:200px;top:108px;width:800px;text-align:center;font-size:13.5px;line-height:24px;color:var(--white)}
.qmark{position:absolute;font-family:Georgia,serif;font-size:56px;color:rgba(255,255,255,.6);line-height:1}
.avatar{position:absolute;left:558px;top:2680px;width:84px;height:84px;border-radius:50%;background:#e9ecef;border:4px solid var(--white)}
.testi .name{position:absolute;left:0;width:1200px;top:318px;text-align:center;font-family:"Raleway";font-weight:600;font-size:17px;color:var(--white)}
.testi .role{position:absolute;left:0;width:1200px;top:343px;text-align:center;font-size:12px;font-weight:600;color:var(--white)}
.t-arrow{position:absolute;top:187px;width:44px;height:44px;border:1.5px solid rgba(255,255,255,.45);transform:rotate(45deg)}

/* footer */
.footer{position:absolute;left:0;top:2882px;width:1200px;height:303px;background:var(--light)}
.footer h4{position:absolute;top:44px;font-size:20px;font-weight:500;color:var(--ink)}
.links{position:absolute;left:97px;top:88px;list-style:none;font-size:12px;line-height:28.5px;color:var(--ink)}
.links li::before{content:"›";margin-right:16px;color:var(--ink)}
.news-note{position:absolute;left:318px;top:80px;width:240px;font-size:12px;line-height:20px;color:var(--ink)}
.field{position:absolute;left:284px;width:262px;height:38px;border:1px solid #dcdde0;background:var(--white);font-size:12px;color:var(--muted);padding:10px 14px}
.subscribe{left:284px;top:220px;width:126px;height:38px;background:var(--blue);font-size:12px;font-weight:600}
.tweet{position:absolute;left:614px;width:250px;font-size:11.6px;line-height:20px;color:var(--ink);padding-left:32px}
.tweet i{position:absolute;left:2px;top:6px;width:9px;height:9px;border-radius:50%;background:var(--blue)}
.tweet b{color:var(--blue);font-weight:400}
.contact{position:absolute;left:905px;width:250px;font-size:11.6px;line-height:20px;color:var(--ink);padding-left:34px}
.contact svg{position:absolute;left:0;top:3px}
.socials{position:absolute;left:905px;top:218px;display:flex;gap:16px;font-family:"Open Sans",sans-serif;font-size:11px;color:var(--ink)}
.copy{position:absolute;left:0;top:3185px;width:1200px;height:52px;background:var(--bar);font-size:11.5px;color:var(--text);display:flex;align-items:center;justify-content:center}
</style>
</head>
<body>

<header class="hero">
  <div class="hero-photo" role="img" aria-label="Photo of a smiling consultant with glasses reviewing papers with a colleague in a bright office"></div>
  <nav class="nav">
    <div class="logo"><b>MARROWIND</b> IT Consultancy</div>
    <div class="menu">
      <a class="active">HOME</a><a>ABOUT</a><a>SERVICES</a><a>PORTFOLIO</a><a>PRICING</a><a>CONTACT</a>
    </div>
  </nav>
  <span class="arrow" style="left:30px"><svg width="30" height="30" viewBox="0 0 30 30"><path d="M17 9l-6 6 6 6" stroke="#fff" stroke-width="1.8" fill="none"/></svg></span>
  <span class="arrow" style="left:1134px"><svg width="30" height="30" viewBox="0 0 30 30"><path d="M13 9l6 6-6 6" stroke="#fff" stroke-width="1.8" fill="none"/></svg></span>
  <div class="hero-copy">
    <div class="l1">WE ARE AN</div>
    <div class="l2">IT SERVICES COMPANY</div>
    <div class="l3">Focused strongly on cloud</div>
  </div>
  <a class="btn hero-btn">Read More</a>
</header>

<section class="welcome">
  <h2 class="section-title" style="top:660px">WELCOME TO THE MARROWIND <span class="accent">IT CONSULTANCY</span></h2>
  <p class="welcome-text">It is a established fact that a reader will be distracted by the readable content of a page when looking at its layout. The point of using Lorem Ipsum is that it has a more-or-less normal distribution of letters, as opposed to using Content here, content here, making it look like readable English. Many desktop publishing packages and web page editors now use Lorem Ipsum as their default model text, a search for lorem ipsum will uncover many web sites still in their infancy. Various versions have evolved over the years, sometimes</p>
  <a class="btn btn-blue" style="left:375px;top:848px;width:210px;height:56px">Read More About us</a>
  <a class="btn btn-dark" style="left:615px;top:848px;width:210px;height:56px">View More feature</a>
</section>

<section class="why">
  <div class="why-box">
    <h3>WHY US?</h3>
    <p>Contrary to popular belief, Lorem Ipsum is not simply random text.</p>
    <a class="btn">Learn More</a>
  </div>
  <div class="platform" style="left:421px"><div class="mark"></div><h4>CLOUD QNT</h4><p>There are many variations of passages to the past</p></div>
  <div class="platform" style="left:641px"><div class="mark"></div><h4>VANTREL SKYLINE</h4><p>There are many variations of passages to the past</p></div>
  <div class="platform" style="left:874px"><div class="mark"></div><h4>HORVIK VAPOR</h4><p>There are many variations of passages to the past</p></div>
</section>

<section class="who">
  <h2 class="section-title" style="top:1258px">WHO <span class="accent">WE ARE</span></h2>
  <div class="who-text">
    <p>Lorem ipsum dolor sit amet, consectetur adipiscing elit, sed do eiusmod tempor incididunt ut labore et dolore magna aliqua. Ut enim ad minim veniam, quis nostrud exercitation ullamco laboris nisi ut aliquip ex. Suspendisse aliquet imperdiet commodo. Aenean vel lacinia elit. Class aptent taciti sociosqu ad litora torquent per.</p>
    <p>Sed eget pulvinar quam, vel feugiat enim. Aliquam erat volutpat. Phasellus eu porta ipsum. Suspendisse aliquet imperdiet commodo. Aenean vel lacinia elit. Class aptent taciti sociosqu ad litora torquent per. Vestibulum velmo.</p>
    <ul class="ticks">
      <li><svg width="12" height="10" viewBox="0 0 12 10"><path d="M1 5l3.5 3.5L11 1" stroke="#555" stroke-width="1.8" fill="none"/></svg>Etiam sed dolor ac diam volutpat</li>
      <li><svg width="12" height="10" viewBox="0 0 12 10"><path d="M1 5l3.5 3.5L11 1" stroke="#555" stroke-width="1.8" fill="none"/></svg>Sed eget pulvinar quam, vel feugiat enim aliquam</li>
      <li><svg width="12" height="10" viewBox="0 0 12 10"><path d="M1 5l3.5 3.5L11 1" stroke="#555" stroke-width="1.8" fill="none"/></svg>Erat volutpat. Phasellus eu porta ipsum suspendisse aliquet imperdiet</li>
      <li><svg width="12" height="10" viewBox="0 0 12 10"><path d="M1 5l3.5 3.5L11 1" stroke="#555" stroke-width="1.8" fill="none"/></svg>Phasellus eu porta ipsum. Suspendisse aliquet imperdiet commodo</li>
    </ul>
  </div>
  <div class="screen" role="img" aria-label="Laptop screen showing the Marrowind home page"></div>
  <div class="laptop-base"></div>
</section>

<section class="offers" role="img" aria-label="Dark background photo of a desk workspace">
  <h2>DON'T MISS <span class="accent">OUT OUR OFFERS</span></h2>
  <p>Lorem ipsum dolor sit amet, consectetur adipisicing elit, sed do eiusmod tempor incididunt ut labore et dolore magna aliqua. Ut enim ad minim veniam, quis nostrud exercitation ullamco laboris nisi ut aliquip ex.</p>
  <a class="btn btn-blue">Contact us Now</a>
</section>

<section class="services">
  <h2 class="section-title" style="top:1897px">OUR <span class="accent">SERVICES</span></h2>
  <div class="vline" style="left:431px;top:1985px;height:420px"></div>
  <div class="vline" style="left:772px;top:1985px;height:420px"></div>

  <div class="service" style="left:97px;top:1985px">
    <svg width="80" height="48" viewBox="0 0 80 48" fill="none" stroke="#333" stroke-width="1.6"><circle cx="28" cy="24" r="16"/><path d="M20 37l-6 6 2-9"/><circle cx="52" cy="24" r="16"/><path d="M60 37l6 6-2-9"/></svg>
    <h4>SUSTAINABLY EMBRACE</h4>
    <p>At vero eos et accusamus et iusto odio ducimus qui blanditiis praesentium voluptatum deleniti atque corrupti quos dolores</p>
    <a class="more">Read More</a>
  </div>
  <div class="service" style="left:431px;top:1985px">
    <svg width="80" height="48" viewBox="0 0 80 48" fill="none" stroke="#333" stroke-width="1.6"><path d="M26 36h30a10 10 0 0 0 0-20 14 14 0 0 0-27-2 11 11 0 0 0-3 22z"/><circle cx="40" cy="26" r="4"/><circle cx="32" cy="42" r="3"/><circle cx="48" cy="42" r="3"/></svg>
    <h4>CLOUD PLATFORMS</h4>
    <p>At vero eos et accusamus et iusto odio ducimus qui blanditiis praesentium voluptatum deleniti atque corrupti quos dolores</p>
    <a class="more">Read More</a>
  </div>
  <div class="service" style="left:772px;top:1985px">
    <svg width="80" height="48" viewBox="0 0 80 48" fill="none" stroke="#333" stroke-width="1.6"><path d="M28 34h-2a10 10 0 0 1 0-20 14 14 0 0 1 27-2 10 10 0 0 1 3 22h-2"/><path d="M36 40V26m-5 5l5-5 5 5M46 24v14m-5-5l5 5 5-5"/></svg>
    <h4>TRANSFORMING PRACTICES</h4>
    <p>At vero eos et accusamus et iusto odio ducimus qui blanditiis praesentium voluptatum deleniti atque corrupti quos dolores</p>
    <a class="more">Read More</a>
  </div>

  <div class="service" style="left:97px;top:2222px">
    <svg width="80" height="56" viewBox="0 0 80 56" fill="none" stroke="#333" stroke-width="1.6"><circle cx="40" cy="16" r="11"/><path d="M20 54c0-13 9-22 20-22s20 9 20 22z"/><path d="M36 32l4 10 4-10"/></svg>
    <h4>SKILLS AND TECHNOLOGY</h4>
    <p>At vero eos et accusamus et iusto odio ducimus qui blanditiis praesentium voluptatum deleniti atque corrupti quos dolores</p>
    <a class="more">Read More</a>
  </div>
  <div class="service" style="left:431px;top:2222px">
    <svg width="80" height="56" viewBox="0 0 80 56" fill="none" stroke="#333" stroke-width="1.6"><path d="M35 2h10l-2 8h-6z"/><path d="M37 10l-5 32 8 10 8-10-5-32"/></svg>
    <h4>DEVOPS AND SECURITY</h4>
    <p>At vero eos et accusamus et iusto odio ducimus qui blanditiis praesentium voluptatum deleniti atque corrupti quos dolores</p>
    <a class="more">Read More</a>
  </div>
  <div class="service" style="left:772px;top:2222px">
    <svg width="80" height="56" viewBox="0 0 80 56" fill="none" stroke="#333" stroke-width="1.6"><circle cx="40" cy="28" r="22"/><path d="M40 28V14a14 14 0 1 0 14 14z"/><path d="M44 24V12a16 16 0 0 1 12 12z"/></svg>
    <h4>IT SERVICES</h4>
    <p>At vero eos et accusamus et iusto odio ducimus qui blanditiis praesentium voluptatum deleniti atque corrupti quos dolores</p>
    <a class="more">Read More</a>
  </div>
</section>

<section class="testi" role="img" aria-label="Blue tinted photo of business people in a meeting">
  <h2>What Our Client <span>Say About Us</span></h2>
  <span class="qmark" style="left:178px;top:96px">&ldquo;</span>
  <p class="quote">There are many variations of passages of Lorem Ipsum available, but the majority have suffered alteration in some form, by injected humour, or randomised words which don't look even slightly believable. If you are going to use a passage There are many variations of passages of Lorem Ipsum available, but the majority have suffered alteration</p>
  <span class="qmark" style="left:980px;top:150px">&rdquo;</span>
  <span class="t-arrow" style="left:52px"></span>
  <span class="t-arrow" style="left:1104px"></span>
  <div class="name">Dana Whitlow</div>
  <div class="role">Heart Patient</div>
</section>
<div class="avatar" role="img" aria-label="Client portrait"></div>

<footer class="footer">
  <h4 style="left:97px">Quick Links</h4>
  <ul class="links">
    <li>About us</li><li>Service</li><li>Our success Stories</li><li>Projects</li><li>Blog</li><li>Contact us</li>
  </ul>

  <h4 style="left:284px">NewsLetter</h4>
  <svg class="abs" style="left:286px;top:84px" width="20" height="18" viewBox="0 0 20 18"><path d="M1 8L19 1l-4 16-5-5-3 4V10z" fill="#222"/></svg>
  <p class="news-note">Sign up with your name and email to get updates fresh updates.</p>
  <div class="field" style="top:124px">Name</div>
  <div class="field" style="top:170px">Email id</div>
  <a class="btn subscribe">SUBSCRIBE NOW</a>

  <h4 style="left:614px">Latest Tweets</h4>
  <div class="tweet" style="top:84px"><i></i><b>@ MConsultancy</b> It is a long established fact that a reader will distracted</div>
  <div class="tweet" style="top:148px"><i></i><b>@ MConsultancy</b> It is a long established fact that a reader will distracted</div>
  <div class="tweet" style="top:212px"><i></i><b>@ MConsultancy</b> It is a long established fact that a reader will distracted</div>

  <h4 style="left:905px">Get In Touch</h4>
  <div class="contact" style="top:84px"><svg width="14" height="13" viewBox="0 0 14 13"><path d="M7 1L1 6h2v6h3V8h2v4h3V6h2z" fill="#444"/></svg>The generated Lorem Ipsum is therefore always</div>
  <div class="contact" style="top:130px"><svg width="13" height="13" viewBox="0 0 13 13"><path d="M3 1l2 3-1.5 1.5a8 8 0 0 0 4 4L9 8l3 2-1 2.5C5 12 1 8 .5 2z" fill="#444"/></svg>+61 2 5550 1842 / 5550 7731</div>
  <div class="contact" style="top:160px"><svg width="14" height="11" viewBox="0 0 14 11"><rect x=".5" y=".5" width="13" height="10" fill="none" stroke="#444"/><path d="M.5 .5L7 6l6.5-5.5" fill="none" stroke="#444"/></svg>info@marrowind-mail.com</div>
  <div class="socials"><span>Orvo</span><span>Tesk</span><span>Lumo</span><span>Kindi</span><span>Plaz</span></div>
</footer>
<div class="copy">Copyright@2016 Company Name , all rights Reserved</div>

</body>
</html>
```